redesign of my existing custom website into Wordpress based website

I need someone to redesign my current website into something more classy, simplistic, modern and on trend. I would like it set up on Wordpress in a way thats easy for me to make my own additions to blogs/price changes and promotion banners. I will also need a page that is password protected so members can login and have access to all my training videos and resources.
website is www.tidewellmamas.com.au

Target Market(s)

new mums

Industry/Entity Type

Fitness

Coding

Coded - Design and coding required

Number of Pages Required

5+ page

Colors
33a6d7

Requirements
Must have
• chic, modern, stylish and simplistic.
• a call to action above the page fold
• mobile friendly conversion
• a pop up message as soon as someone enters my sight offering my free report
• a members page that is password protected containing 3 youtube videos and 6 pdf attachments as resources
• a home page
• a contact us page
• an about us page
• a blog page
• a store page
Nice to have
• some examples of my peers websites that I like:
• www.norapellwick.com
• https://www.9qlr.com
• https://41bytedgarth.com
Should not have
• anything gimmicky

```html
<!DOCTYPE html>
<html lang="en">
<head>
<meta charset="utf-8">
<title>Tidewell Mamas – 12 Week Home Workout Program</title>
<link href="https://fonts.googleapis.com/css2?family=Oswald:wght@400;500&family=Open+Sans:wght@400;600;700&display=swap" rel="stylesheet">
<style>
:root{
  --brand:#33a6d7;
  --brand-dark:#2b93c1;
  --pink:#c2185b;
  --hero:#55606d;
  --hero-dark:#3e4752;
  --ink:#333b44;
  --muted:#6d737a;
  --soft:#f4f5f8;
  --line:#e3e6ea;
  --footer:#3d3d3f;
  --white:#ffffff;
}
*{box-sizing:border-box;margin:0;padding:0}
html,body{width:1200px;height:3830px;overflow:hidden}
body{position:relative;font-family:"Open Sans",Arial,sans-serif;color:var(--ink);background:var(--white)}
.abs{position:absolute}
.heading{font-family:"Oswald",Arial Narrow,sans-serif;font-weight:500;text-transform:uppercase}
.btn{position:absolute;display:flex;align-items:center;justify-content:center;font-family:"Oswald",sans-serif;font-size:17px;text-transform:uppercase;color:var(--white);letter-spacing:.3px;text-decoration:none}
.btn-outline{border:2px solid var(--white)}
.btn-solid{background:var(--brand);border:2px solid var(--white)}
.photo{position:absolute}

/* hero */
.hero{position:absolute;left:0;top:0;width:1200px;height:633px;background:radial-gradient(ellipse at 40% 40%,#68727e,var(--hero) 55%,var(--hero-dark))}
.logo-badge{position:absolute;left:133px;top:-10px;width:180px;height:180px;border-radius:50%;background:var(--white);display:flex;align-items:center;justify-content:center;text-align:center}
.logo-badge span{font-family:"Oswald",sans-serif;font-weight:500;font-size:24px;color:var(--pink);line-height:1.1}
.nav{position:absolute;top:26px;left:400px;font-family:"Oswald",sans-serif;font-size:18px;color:var(--white)}
.nav a{position:absolute;white-space:nowrap;text-decoration:none;color:var(--white);top:0}
.nav .current{border:2px solid var(--white);padding:2px 14px;top:-4px}
.hero-title{position:absolute;left:133px;top:240px;font-family:"Oswald",sans-serif;font-size:46px;line-height:1.2;color:var(--white);font-weight:400}
.hero-sub{position:absolute;left:133px;top:472px;font-family:"Oswald",sans-serif;font-size:25px;line-height:1.35;color:#c9cfd6;font-weight:400}
.hero-price{position:absolute;left:419px;top:478px;font-family:"Oswald",sans-serif;font-size:20px;line-height:1.4;color:#c9cfd6}
.hero-price b{color:var(--white);font-weight:400}
.slider-dots{position:absolute;left:1155px;top:290px;display:flex;flex-direction:column;gap:10px}
.slider-dots i{display:block;width:10px;height:10px;border-radius:50%;background:rgba(255,255,255,.5)}
.slider-dots i:first-child{background:var(--white)}

/* why */
.why{position:absolute;left:0;top:633px;width:1200px;height:549px;background:var(--soft)}
.section-title{position:absolute;left:0;width:1200px;text-align:center;font-size:26px;color:var(--brand)}
.feature{position:absolute;top:123px;width:290px;height:327px;background:var(--white);box-shadow:0 1px 4px rgba(0,0,0,.12);text-align:center}
.feature .photo{left:0;top:0;width:290px;height:174px}
.feature h3{position:absolute;top:200px;width:100%;font-size:13.5px;font-weight:600;text-transform:uppercase;color:var(--ink)}
.feature p{position:absolute;top:228px;left:22px;right:22px;font-size:12px;line-height:1.6;color:var(--muted)}
.plus{position:absolute;left:125px;top:307px;width:40px;height:40px;border-radius:50%;background:var(--brand);color:var(--white);font-size:26px;line-height:37px;text-align:center}

/* optin */
.optin{position:absolute;left:0;top:1182px;width:1200px;height:567px}
.optin-box{position:absolute;left:730px;top:74px;width:337px;height:393px;background:var(--white);text-align:center}
.optin-box h2{margin-top:30px;font-size:25px;line-height:1.25;color:var(--brand)}
.optin-box p{margin:14px 30px 0;font-size:12.5px;line-height:1.6;color:var(--ink)}
.optin-box p b{color:var(--brand);font-weight:600}
.field{position:absolute;left:28px;width:281px;height:38px;border:1px solid var(--line);font-size:12px;line-height:36px;text-align:left;padding-left:12px;color:var(--ink)}
.optin-box .btn{left:28px;top:318px;width:281px;height:46px;background:var(--brand);border:none}

/* packs */
.pack{position:absolute;left:0;width:1200px;height:352px;background:var(--white)}
.pack h2{position:absolute;font-family:"Oswald",sans-serif;font-weight:400;font-size:22px;color:var(--brand)}
.pack ul{position:absolute;list-style:none;font-size:13px;line-height:2.05;color:var(--ink)}
.pack li{padding-left:20px;position:relative}
.pack li::before{content:"";position:absolute;left:0;top:8px;width:9px;height:9px;border:2px solid var(--brand);border-radius:50%}
.pack .price{position:absolute;font-size:15px;font-weight:600;color:var(--ink)}

/* offer */
.offer{position:absolute;left:0;top:2453px;width:1200px;height:411px;background:var(--brand);color:var(--white)}
.offer .kicker{position:absolute;left:133px;top:85px;font-family:"Oswald",sans-serif;font-size:20px}
.offer h2{position:absolute;left:133px;top:113px;font-family:"Oswald",sans-serif;font-weight:400;font-size:36px;line-height:1.2}
.offer p{position:absolute;left:133px;top:172px;width:630px;font-size:12.5px;line-height:1.6}
.offer .btn{left:133px;top:279px;width:166px;height:48px}

/* news */
.news{position:absolute;left:0;top:2864px;width:1200px;height:531px;background:var(--soft)}
.news .section-title{color:var(--ink);top:62px}
.post{position:absolute;top:138px;width:217px;height:296px;background:var(--white)}
.post .photo{left:0;top:0;width:217px;height:108px}
.post .date{position:absolute;left:12px;top:122px;font-size:11.5px;color:var(--muted)}
.post h3{position:absolute;left:12px;top:150px;font-size:14px;font-weight:600;color:var(--ink)}
.post p{position:absolute;left:12px;right:12px;top:176px;font-size:11.5px;line-height:1.55;color:var(--muted)}
.post .more{position:absolute;left:12px;top:262px;font-size:10.5px;font-weight:700;color:var(--brand);text-transform:uppercase}

/* closing cta */
.closing{position:absolute;left:0;top:3395px;width:1200px;height:261px;text-align:center}
.closing h2{position:absolute;top:64px;width:100%;font-size:26px;color:var(--ink)}
.closing p{position:absolute;top:108px;width:100%;font-family:"Oswald",sans-serif;font-size:20px;color:var(--ink)}
.closing .btn{left:516px;top:160px;width:168px;height:46px;background:var(--brand);border:none}

/* footer */
.footer{position:absolute;left:0;top:3656px;width:1200px;height:174px;background:var(--footer);color:#d4d4d6}
.footer-links{position:absolute;left:133px;top:36px;font-size:12.5px;color:var(--white)}
.footer-links span{margin:0 7px;color:#9a9a9d}
.footer-note{position:absolute;left:133px;top:62px;width:700px;font-size:11.5px;line-height:1.75}
.footer-brand{position:absolute;left:985px;top:22px;display:flex;align-items:center;gap:8px;font-family:"Oswald",sans-serif;font-size:16px;color:var(--white)}
.footer-brand i{display:block;width:34px;height:34px;border-radius:50%;border:2px solid var(--white)}
.social{position:absolute;left:965px;top:102px;display:flex;gap:10px}
.social i{display:block;width:34px;height:34px;border-radius:50%;border:2px solid var(--white)}
</style>
</head>
<body>

<header class="hero">
  <div class="photo" role="img" aria-label="Smiling fit mum in a green zip hoodie, hands on hips" style="left:664px;top:0;width:536px;height:633px;background:linear-gradient(90deg,rgba(85,96,109,0),#7a7f74 35%,#8cc63f 55%,#6a7a5c 80%,rgba(62,71,82,.6))"></div>
  <div class="logo-badge"><span>Tidewell<br>Mamas</span></div>
  <nav class="nav">
    <a class="current" style="left:0">Home</a>
    <a style="left:103px">About Us</a>
    <a style="left:213px">Program</a>
    <a style="left:317px">Blog</a>
    <a style="left:394px">Shop</a>
    <a style="left:476px">Contact</a>
    <a style="left:578px">My cart
      <svg width="34" height="26" viewBox="0 0 34 26" style="vertical-align:-4px;margin-left:4px"><path d="M3 9h18l-2 14H5z" fill="none" stroke="#fff" stroke-width="2"/><path d="M8 9a4 4 0 0 1 8 0" fill="none" stroke="#fff" stroke-width="2"/><circle cx="26" cy="6" r="6" fill="#33a6d7"/><text x="26" y="9" font-size="8" fill="#fff" text-anchor="middle" font-family="Open Sans">0</text></svg>
    </a>
  </nav>
  <h1 class="hero-title">12 Week Home Workout<br>Program For Mums!</h1>
  <a class="btn btn-outline" style="left:133px;top:390px;width:163px;height:50px">Get Started Now</a>
  <a class="btn btn-solid" style="left:309px;top:390px;width:128px;height:50px">Watch Now</a>
  <p class="hero-sub">Start seeing amazing results<br>in just a few weeks!</p>
  <p class="hero-price">Starting from<br><b>only $7.50 per week!</b></p>
  <div class="slider-dots"><i></i><i></i><i></i></div>
</header>

<section class="why">
  <h2 class="section-title heading" style="top:68px">Why our program is different</h2>
  <article class="feature" style="left:133px">
    <div class="photo" role="img" aria-label="Mum exercising on a mat with her baby" style="background:linear-gradient(135deg,#5a3b3c,#b9506e 50%,#7a4a5a)"></div>
    <h3>Specially designed for mums</h3>
    <p>Unlike other home workout programs out ours is designed specially for mums. Because our bodies go through such a major change.</p>
    <div class="plus">+</div>
  </article>
  <article class="feature" style="left:457px">
    <div class="photo" role="img" aria-label="Toddler climbing on a step platform with dumbbells" style="background:linear-gradient(135deg,#8a6a5a,#d9a7b0 50%,#6a5b52)"></div>
    <h3>Workout equipment</h3>
    <p>Unlike other home workout programs out ours is designed specially for mums. Because our bodies go through such a major change.</p>
    <div class="plus">+</div>
  </article>
  <article class="feature" style="left:779px">
    <div class="photo" role="img" aria-label="Mum feeding her child at home" style="background:linear-gradient(135deg,#7a5a4a,#c9a38a 50%,#9a5a6a)"></div>
    <h3>Delicious low fat family</h3>
    <p>Unlike other home workout programs out ours is designed specially for mums. Because our bodies go through such a major change.</p>
    <div class="plus">+</div>
  </article>
</section>

<section class="optin">
  <div class="photo" role="img" aria-label="Mum lifting dumbbells on the floor beside her toddler in a bright living room" style="left:0;top:0;width:1200px;height:567px;background:linear-gradient(90deg,#d8d4cc,#ece9e3 30%,#f2f0ec 60%,#e6e3dd)"></div>
  <form class="optin-box">
    <h2 class="heading">Get your free top 10<br>baby belly blasting tips</h2>
    <p>See our secret tips to a flatter yummy mummy tummy that you can start implementing for <b>FREE TODAY!</b></p>
    <div class="field" style="top:168px">Name:</div>
    <div class="field" style="top:212px">Email:</div>
    <div class="field" style="top:256px">Phone:</div>
    <a class="btn">Get it free now</a>
  </form>
</section>

<section class="pack" style="top:1749px">
  <h2 style="left:133px;top:62px">12 week Home Workout Program - Equipment Pack</h2>
  <ul style="left:133px;top:108px">
    <li>Our unique 3 stage, 12 week training program</li>
    <li>Full Instructional Workout DVD and program cards for each program</li>
    <li>Weekly accountability charts</li>
    <li>Weekly coaching emails</li>
    <li>Funky exercise equipment for your home</li>
    <li>Nutritionist approved healthy eating guide</li>
  </ul>
  <p class="price" style="left:150px;top:296px">That's only $10.60 per week!</p>
  <div class="photo" role="img" aria-label="Close-up of hands lifting colourful dumbbells from a rack" style="left:600px;top:0;width:600px;height:352px;background:linear-gradient(135deg,#3a3230,#7a5a4a 40%,#c0392b 55%,#2f6fb0 70%,#2a2624)"></div>
</section>

<section class="pack" style="top:2101px">
  <div class="photo" role="img" aria-label="Mum sitting on an exercise mat in front of a leather couch" style="left:0;top:0;width:600px;height:352px;background:linear-gradient(135deg,#2e2624,#5a4a44 40%,#a38aa0 70%,#5b4f8a)"></div>
  <h2 style="left:638px;top:62px">12 week Home Workout Program - Basic Pack</h2>
  <ul style="left:638px;top:108px">
    <li>Our 3 stage, 12 week training program</li>
    <li>Full Instructional Workout DVD for each program</li>
    <li>Weekly accountability charts</li>
    <li>Weekly coaching emails</li>
    <li>Nutritionist approved Healthy eating guidelines</li>
    <li>Healthy Family Favourites recipe ebook</li>
  </ul>
  <p class="price" style="left:655px;top:277px">That's only $7.50 per week!</p>
</section>

<section class="offer">
  <p class="kicker">Starting from only $7.50 per week!</p>
  <h2>Already have the equipment you need?</h2>
  <p>Sed ut perspiciatis unde omnis iste natus error sit voluptatem accusantium doloremque laudantium, totam rem aperiam, eaque ipsa quae ab illo inventore veritatis et quasi architecto beatae vitae dicta sunt explicabo nemo enim ipsam voluptatem quia voluptas sit aspernatur. Eaque ipsa quae ab illo inventore veritatis et quasi architecto beatae vitae dicta sunt explicabo.</p>
  <a class="btn btn-outline">Get Started Now</a>
  <div class="photo" role="img" aria-label="Program DVD case and printed recipe book" style="left:779px;top:95px;width:288px;height:235px;background:linear-gradient(135deg,#e8e2dc,#c85a8a 45%,#6a8a4a 75%,#d9cfc4)"></div>
  <svg class="abs" style="left:935px;top:110px" width="110" height="110" viewBox="0 0 110 110">
    <circle cx="55" cy="55" r="52" fill="#33a6d7" stroke="#fff" stroke-width="3"/>
    <text x="55" y="56" text-anchor="middle" font-family="Oswald, sans-serif" font-size="26" fill="#fff">FREE</text>
    <text x="55" y="78" text-anchor="middle" font-family="Oswald, sans-serif" font-size="15" fill="#fff">Postage</text>
  </svg>
</section>

<section class="news">
  <h2 class="section-title heading">Latest News</h2>
  <article class="post" style="left:133px">
    <div class="photo" role="img" aria-label="Mum training with her child" style="background:linear-gradient(135deg,#6a4a3a,#c98a6a 50%,#8a5a4a)"></div>
    <span class="date">&#9783; Jan 03, 2017</span>
    <h3>The benefits of training</h3>
    <p>Cras mattis consectetur purus sit amet fermentum lorem ipsum, porta acco nsectetur arvestibulum.</p>
    <span class="more">Read more</span>
  </article>
  <article class="post" style="left:373px">
    <div class="photo" role="img" aria-label="Bowl of pumpkin soup" style="background:radial-gradient(circle at 50% 55%,#e0a020,#f0c050 35%,#f4f1ea 60%)"></div>
    <span class="date">&#9783; Jan 03, 2017</span>
    <h3>Creamy Pumpkin Soup</h3>
    <p>Cras mattis consectetur purus sit amet fermentum lorem ipsum, porta acco nsectetur arvestibulum.</p>
    <span class="more">Read more</span>
  </article>
  <article class="post" style="left:610px">
    <div class="photo" role="img" aria-label="Dumbbells and water bottle on a mat" style="background:linear-gradient(135deg,#b05a8a,#6ac0c0 45%,#c8c0b8)"></div>
    <span class="date">&#9783; Jan 03, 2017</span>
    <h3>Cardio workout</h3>
    <p>Cras mattis consectetur purus sit amet fermentum lorem ipsum, porta acco nsectetur arvestibulum.</p>
    <span class="more">Read more</span>
  </article>
  <article class="post" style="left:850px">
    <div class="photo" role="img" aria-label="Woman doing an exercise on a mat" style="background:linear-gradient(135deg,#3a2e2c,#8a3a4a 50%,#4a4a8a)"></div>
    <span class="date">&#9783; Jan 03, 2017</span>
    <h3>Marisol's 10 exercise</h3>
    <p>Cras mattis consectetur purus sit amet fermentum lorem ipsum, porta acco nsectetur arvestibulum.</p>
    <span class="more">Read more</span>
  </article>
</section>

<section class="closing">
  <h2 class="heading">Take the first step today by joining our program</h2>
  <p>and let us help you bounce back to the body that you deserve!</p>
  <a class="btn">Get Started Now</a>
</section>

<footer class="footer">
  <div class="footer-links">Home<span>|</span>About Us<span>|</span>Programs<span>|</span>Blog<span>|</span>Shop<span>|</span>Contact<span>|</span>Website Policies</div>
  <p class="footer-note">Before you begin any type of exercise post baby, you must ensure you get the ok from your doctor or obstetrician.<br>Its essential you give your body the appropriate amount of time to fully recover before attempting any form of exercise.<br>Copyright © 2017 Tidewell Mamas. All rights reserved.</p>
  <div class="footer-brand"><i></i>Tidewell Mamas</div>
  <div class="social" aria-label="Social links"><i></i><i></i><i></i><i></i></div>
</footer>

</body>
</html>
```